Design my site www.brieflyledger.com

So here is what I am thinking in terms of design:

https://plenvo.com

https://www.skyluxair.com

http://kalvex.com/harbor-plaza-tower/

I want the theme to be white and blue (royal blue). I attached a paint picture of what I would like the site to look like in terms of placing the text. Generally, what I like about the sites above is that they are simple, you can navigate easily and have some kind of idea of what's going on by looking at the center (picture and motto). Let's establish a clear understanding of how the functional part of the site would look like. Please see the picture attached.

I want to keep it simple: On top would be the Name 'BRIEFLY ledger", somewhere to the right on top on the page would be 'Sign in" button.

In the center would be a picture (maybe a video) with the Motto (on top of it all in capital) OBSERVE NAVIGATE DECIDE and below would be the "sign up now"

Below the picture (like on kalvex.com site) or to the left on top of the page would be "About Us', "Press" "Contact Us' buttons.

Then once the user gets to his page his got 3 tabs " Press Headlines", "Events", " Briefings".

we would keep the same format I only have on the site, but separate for every Tab.

I do not want the user to get distracted. I also want him to be able to access the page though mobile phone and be able to get automatic updates just like Zorvan Pings without having to sign in daily.

The landing page must be minimalist yet with business/corporate feel where users can navigate easily and a "what you see is what you get" approach. You want an image or video (personally I prefer the video.. it does capture the users attention instantly, as long as it is an interesting video), with your taglines in it.

Sections available to public: About Us, Contact Us, Landing Page with Signup Option

Private: Public Sections + User Account Page, Tabs for (Events, Press Headlines, Briefings)

Target Market(s)

PR/media monitoring/diplomatic community

Coding

Coded - Design and coding required

Number of Pages Required

1 page

Font styles to use
Serif
Sans Serif

Colors
0255a3
ec1f27

Requirements
Must have
• a simple landing page, that is user friendly.
Nice to have
• a video with the explanation of how to navigate the site
Should not have
• too many colors, graphs etc.

```html
<!DOCTYPE html>
<html lang="en">
<head>
<meta charset="utf-8">
<title>Briefly Ledger — Newspapers Headlines</title>
<link rel="stylesheet" href="https://fonts.googleapis.com/css2?family=Arimo:wght@400;700&family=Open+Sans:wght@400;600;700&display=swap">
<style>
:root{
  --blue:#0255a3;
  --dark:#1b1b1b;
  --tab-line:#4a4a4a;
  --title:#333333;
  --body:#6e6e6e;
  --rule:#dcdcdc;
  --white:#ffffff;
}
*{box-sizing:border-box;margin:0;padding:0}
html,body{width:1172px;height:1200px;overflow:hidden;background:var(--white)}
body{display:flex;flex-direction:column;font-family:"Open Sans",Arial,sans-serif;border-top:4px solid var(--blue)}
.wrap{width:979px;margin:0 auto}
.site-header{height:76px}
.site-header .wrap{height:100%;display:flex;align-items:center;justify-content:space-between}
.brand{font-family:Arimo,Arial,sans-serif;font-weight:700;font-size:22px;color:#2a2a2a;letter-spacing:.2px;margin-top:2px}
.account{display:flex;align-items:center;gap:18px;margin-top:-4px}
.avatar{width:56px;height:56px;border-radius:50%;border:3px solid #eee;background:radial-gradient(circle at 50% 40%,#c9a48a 0,#8a7466 55%,#5d5a5a 100%)}
.account-name{font-family:Arimo,Arial,sans-serif;font-size:14px;font-weight:700;color:#444}
.tab-bar{background:var(--dark);height:64px}
.tabs{display:flex;height:100%}
.tab{flex:1;display:flex;align-items:center;justify-content:center;gap:16px;color:var(--white);font-family:Arimo,Arial,sans-serif;font-weight:700;font-size:17px;text-transform:uppercase;border-left:1px solid var(--tab-line);border-bottom:1px solid var(--tab-line)}
.tab:last-child{border-right:1px solid var(--tab-line)}
.tab.is-active{background:var(--blue);border-color:var(--blue);justify-content:flex-start;padding-left:30px}
.tab svg{fill:var(--white)}
.feed{padding-top:57px}
.story{display:grid;grid-template-columns:286px 1fr;column-gap:32px;padding-bottom:27px;border-bottom:1px solid var(--rule);margin-bottom:26px}
.story-photo{height:239px}
.photo-conference{background:linear-gradient(180deg,#eef0f6 0%,#e6dce4 35%,#5a5450 65%,#2c2a2c 85%,#b88e45 100%)}
.photo-speaker{background:linear-gradient(100deg,#dfe7f2 0%,#d9dbe3 35%,#3b4a78 55%,#ece3cf 80%,#f0d598 100%)}
.photo-duo{background:linear-gradient(110deg,#d8cabc 0%,#b9a999 30%,#2a2a30 50%,#8bb2dc 72%,#e3d6c6 100%)}
.story-title{font-family:Arimo,Arial,sans-serif;font-size:17.5px;font-weight:400;color:var(--title);margin-top:-4px;line-height:1.3}
.story-meta{display:flex;align-items:center;gap:9px;margin-top:11px;color:var(--blue);font-size:13.8px}
.story-meta span{display:flex;align-items:center;gap:7px}
.story-meta svg{fill:var(--blue)}
.story-meta .sep{color:var(--blue)}
.story-text{margin-top:14px;font-size:12.8px;line-height:25px;color:var(--body)}
.read-more{display:inline-block;margin-top:9px;font-size:12.8px;font-weight:700;color:var(--blue);text-decoration:none}
.site-footer{margin-top:auto;height:90px;background:var(--blue);color:var(--white)}
.site-footer .wrap{height:100%;display:flex;align-items:center;justify-content:space-between}
.footer-links{font-size:12.8px;display:flex;gap:9px;margin-left:2px}
.footer-links a{color:var(--white);text-decoration:none}
.copyright{font-size:12.8px;margin-top:12px}
.social{display:flex;gap:6px}
.social span{width:38px;height:38px;border:2px solid var(--white);border-radius:50%}
</style>
</head>
<body>
<header class="site-header">
  <div class="wrap">
    <div class="brand">BRIEFLY LEDGER</div>
    <div class="account">
      <div class="avatar" role="img" aria-label="Portrait of the signed-in user"></div>
      <div class="account-name">DAREN</div>
    </div>
  </div>
</header>

<nav class="tab-bar">
  <div class="wrap tabs">
    <div class="tab is-active">
      <svg width="34" height="24" viewBox="0 0 34 24"><path d="M4 2h30v20a2 2 0 0 1-2 2H3a3 3 0 0 1-3-3V6h4zm2 2v18h26V4zM2 8v13a1 1 0 0 0 2 0V8zm6-2h10v9H8zm2 2v5h6V8zm10-2h10v2H20zm0 4h10v2H20zm0 4h10v2H20zM8 18h22v2H8z"/></svg>
      Newspapers Headlines
    </div>
    <div class="tab">
      <svg width="28" height="30" viewBox="0 0 28 30"><path d="M6 0h3v5H6zm13 0h3v5h-3zM0 3h5v3h5V3h8v3h5V3h5v27H0zm2 8v17h24V11zm2 2h4v4H4zm6 0h4v4h-4zm6 0h4v4h-4zm6 0h3v4h-3zM4 19h4v4H4zm6 0h4v4h-4zm6 0h4v4h-4zm6 0h3v4h-3z"/></svg>
      Events
    </div>
    <div class="tab">
      <svg width="26" height="32" viewBox="0 0 26 32"><path d="M0 0h17l9 9v23H0zm16 1v9h9zM6 16h14v2H6zm0 5h14v2H6zm0 5h14v2H6z"/></svg>
      Daily Briefing
    </div>
  </div>
</nav>

<main class="feed wrap">
  <article class="story">
    <div class="story-photo photo-conference" role="img" aria-label="Audience seated at a conference listening to a presenter"></div>
    <div class="story-body">
      <h2 class="story-title">At vero eos et accusamus et iusto odio dignissimos ducimus qui blandi</h2>
      <div class="story-meta">
        <span><svg width="13" height="14" viewBox="0 0 13 14"><path d="M3 0h2v2h3V0h2v2h3v12H0V2h3zM1 5v8h11V5zm1 1h2v2H2zm3 0h2v2H5zm3 0h2v2H8zM2 9h2v2H2zm3 0h2v2H5zm3 0h2v2H8z"/></svg>25/06/2016</span>
        <span class="sep">|</span>
        <span><svg width="12" height="14" viewBox="0 0 12 14"><circle cx="6" cy="4" r="3.5"/><path d="M0 14c0-4 2.5-6 6-6s6 2 6 6z"/></svg>Admin</span>
        <span class="sep">|</span>
        <span><svg width="16" height="13" viewBox="0 0 16 13"><ellipse cx="6.5" cy="5" rx="6.5" ry="5"/><path d="M2 8l-1 4 4-2zM9 11a6 5 0 0 0 6-6 5 4 0 0 1-1 7l1 1-3-1z"/></svg>Comment</span>
      </div>
      <p class="story-text">Nam libero tempore, cum soluta nobis est eligendi optio cumque nihil impedit quo minus id quod maxime placea acere possimus, omnis voluptas assumenda est, omnis dolor repellendus. Temporibus autem quibusdam et aut officiis debitis aut rerum necessitatibus saepe eveniet ut et voluptates repudiandae sint et molestiae nonrecusan da e earum rerum hic tenetur a sapiente delectusaut reic.On the other hand, we denounce with righteous indign ation and dislike men who are so beguiled and demoralized by the charms of pleasure of the moment, so blinde desire, that th&nbsp; est et expedita distinctio.</p>
      <a class="read-more" href="#">READ MORE &gt;&gt;</a>
    </div>
  </article>

  <article class="story">
    <div class="story-photo photo-speaker" role="img" aria-label="Woman speaking at a podium microphone"></div>
    <div class="story-body">
      <h2 class="story-title">At vero eos et accusamus et iusto odio dignissimos ducimus qui blandi</h2>
      <div class="story-meta">
        <span><svg width="13" height="14" viewBox="0 0 13 14"><path d="M3 0h2v2h3V0h2v2h3v12H0V2h3zM1 5v8h11V5zm1 1h2v2H2zm3 0h2v2H5zm3 0h2v2H8zM2 9h2v2H2zm3 0h2v2H5zm3 0h2v2H8z"/></svg>25/06/2016</span>
        <span class="sep">|</span>
        <span><svg width="12" height="14" viewBox="0 0 12 14"><circle cx="6" cy="4" r="3.5"/><path d="M0 14c0-4 2.5-6 6-6s6 2 6 6z"/></svg>Admin</span>
        <span class="sep">|</span>
        <span><svg width="16" height="13" viewBox="0 0 16 13"><ellipse cx="6.5" cy="5" rx="6.5" ry="5"/><path d="M2 8l-1 4 4-2zM9 11a6 5 0 0 0 6-6 5 4 0 0 1-1 7l1 1-3-1z"/></svg>Comment</span>
      </div>
      <p class="story-text">Nam libero tempore, cum soluta nobis est eligendi optio cumque nihil impedit quo minus id quod maxime placea acere possimus, omnis voluptas assumenda est, omnis dolor repellendus. Temporibus autem quibusdam et aut officiis debitis aut rerum necessitatibus saepe eveniet ut et voluptates repudiandae sint et molestiae nonrecusan da e earum rerum hic tenetur a sapiente delectusaut reic.On the other hand, we denounce with righteous indign ation and dislike men who are so beguiled and demoralized by the charms of pleasure of the moment, so blinde desire, that th&nbsp; est et expedita distinctio.</p>
      <a class="read-more" href="#">READ MORE &gt;&gt;</a>
    </div>
  </article>

  <article class="story">
    <div class="story-photo photo-duo" role="img" aria-label="Two presenters holding microphones in front of an audience"></div>
    <div class="story-body">
      <h2 class="story-title">At vero eos et accusamus et iusto odio dignissimos ducimus qui blandi</h2>
      <div class="story-meta">
        <span><svg width="13" height="14" viewBox="0 0 13 14"><path d="M3 0h2v2h3V0h2v2h3v12H0V2h3zM1 5v8h11V5zm1 1h2v2H2zm3 0h2v2H5zm3 0h2v2H8zM2 9h2v2H2zm3 0h2v2H5zm3 0h2v2H8z"/></svg>25/06/2016</span>
        <span class="sep">|</span>
        <span><svg width="12" height="14" viewBox="0 0 12 14"><circle cx="6" cy="4" r="3.5"/><path d="M0 14c0-4 2.5-6 6-6s6 2 6 6z"/></svg>Admin</span>
        <span class="sep">|</span>
        <span><svg width="16" height="13" viewBox="0 0 16 13"><ellipse cx="6.5" cy="5" rx="6.5" ry="5"/><path d="M2 8l-1 4 4-2zM9 11a6 5 0 0 0 6-6 5 4 0 0 1-1 7l1 1-3-1z"/></svg>Comment</span>
      </div>
      <p class="story-text">Nam libero tempore, cum soluta nobis est eligendi optio cumque nihil impedit quo minus id quod maxime placea acere possimus, omnis voluptas assumenda est, omnis dolor repellendus. Temporibus autem quibusdam et aut officiis debitis aut rerum necessitatibus saepe eveniet ut et voluptates repudiandae sint et molestiae nonrecusan da e earum rerum hic tenetur a sapiente delectusaut reic.On the other hand, we denounce with righteous indign ation and dislike men who are so beguiled and demoralized by the charms of pleasure of the moment, so blinde desire, that th&nbsp; est et expedita distinctio.</p>
      <a class="read-more" href="#">READ MORE &gt;&gt;</a>
    </div>
  </article>
</main>

<footer class="site-footer">
  <div class="wrap">
    <div>
      <nav class="footer-links">
        <a href="#">Home</a><span>|</span><a href="#">About us</a><span>|</span><a href="#">Press</a><span>|</span><a href="#">Events</a><span>|</span><a href="#">Contact Us</a>
      </nav>
      <p class="copyright">© 2016, Briefly ledger. All rights reserved.</p>
    </div>
    <div class="social" aria-label="Social links">
      <span></span><span></span><span></span><span></span>
    </div>
  </div>
</footer>
</body>
</html>
```